E-Book-Cover für einen Kriminalroman
Zielgruppe
Ich veröffentliche meinen Roman “Die Schwelle” als E-Book.
Das Buch spielt in einer nahen Zukunft, in der Die Schwelle Nachrichten in die Vergangenheit möglich macht. Unfälle und Straftaten werden sofort ungeschehen gemacht. Jeder Bürger kann seinem vergangenen Ich eine Botschaft schicken - und so die eigene Geschichte “reparieren”. Auch Henrik, ein unscheinbarer Projektleiter, erhält eines Tag eine Nachricht aus der Zukunft: 'Halte dich von Maren fern. Sie wird dein Untergang sein'. Die Nachricht stellt Henrik vor ein Rätsel. Vor welcher Gefahr hat er sich gewarnt? Und wer ist Maren? Ein Jahr später wird Henrik durch Zufall Mitwisser einer politischen Verschwörung. Die Killer machen Jagd auf ihn und kennen jeden seiner nächsten Schritte. Die letzte Rettung ist ausgerechnet eine Frau namens Maren.
--- “Die Schwelle” spielt in der Zukunft, ist aber kein Science Fiction Roman. Die beschriebene Welt ist (außer der Zeitmanipulation) wie die unsere. Am ehesten ist das Buch also ein actionreicher Kriminalroman.
Die Hauptzielgruppe sind 25 - 45-jährige, zum Beispiel Leser von Rolf Ebenhöch, Tobias Wendrath oder Karl Vossberg.
Aufgabenstellung
Gewünscht ist ein E-Book-Cover für die Verwendung auf Online-Plattformen wie Kaufora.
Autor: K.J. Brandau
Titel: Die Schwelle
Zusatz: Roman
Visuelle Anforderungen
Das Cover sollte eine Reihe von Türen zeigen. Begründung dazu: Im sogenannten Registerbüro muss der Protagonist in einer von vier nebeneinanderliegenden Türen treten und empfängt dort seine Nachricht aus der Zukunft. Das Thema “Entscheidungen fürs Leben” des Romans wird durch diese Türen visualisiert und als Symbol mehrmals aufgegriffen - dementsprechend ist es aus meiner Sicht perfekt für das Cover.
Für die Fotosuche: Das Registerbüro ist leicht heruntergekommen und wirkt kühl und unsympathisch. Dieses Bild https://de.bildquelle-beispiel.de/id/19384726 (auch noch einmal angehängt) zum Beispiel passt sehr gut.
Thema Hacking und Programmieren
Das Buch spielt in den Lebenswelten von Programmierern und Hackern; Die Schwelle ist eine Datenbank. Dies könnte durch Stil der Schrift oder anders unterstützt werden. Nur, wenn sinnvoll und ohne dass es wie ein Computerbuch aus den 90ern wirkt natürlich :)
- Die Font kann das Thema aufgreifen, aber bitte KEINE Vintage LED-Schrift im Stil von http://www.schriftkiste-beispiel.de/segment-alt.font, sondern eine die einem modernen Monitor entspringt. Entweder verpixelt (Beispiel im Anhang) oder durch eine gepunktete Schrift in hoher "Auflösung" (Beispiel: http://www.schriftkiste-beispiel.de/perlen-raster.font, also nicht nur 7 Punkte in der Breite), hier könnte man die Ränder auch etwas blurren, um den Effekt eines Monitors zu erzielen
- Wenn der o.g. Schriftstil benutzt wird, bitte in Kleinbuchstaben (wie ein Befehl auf dem Terminal)
-> All kein Muss, nur wenn sinnvoll!
Weitere Anforderungen:
- Die Türen befinden sich in einem kühlen, sterilen BÜRO, dementsprechend dürfen sie nicht zu hübsch aussehen oder an Wohnzimmertüren erinnern
- Wenn Codezeilen als Hintergrundbestandteil genutzt..

```html
<!DOCTYPE html>
<html lang="de">
<head>
<meta charset="utf-8">
<title>Die Schwelle – K.J. Brandau</title>
<link rel="stylesheet" href="https://fonts.googleapis.com/css2?family=Doto:wght@900&family=Ubuntu:wght@400&family=Tinos&display=swap">
<style>
  :root {
    --ink-deep: #05080b;
    --code-navy: #0b1a26;
    --code-teal: #123044;
    --author-blue: #3f86ad;
    --roman-blue: #3a7ea6;
    --title-white: #f2f6f8;
    --title-glow: rgba(190, 225, 245, 0.55);
    --floor-teal: #1d4756;
    --room-dark: #070d11;
    --door-light: #c9dce6;
  }
  html, body {
    margin: 0;
    padding: 0;
    overflow: hidden;
    background: var(--ink-deep);
  }
  .cover {
    position: relative;
    width: 750px;
    height: 1200px;
    overflow: hidden;
    background: var(--ink-deep);
  }
  .code-field {
    position: absolute;
    inset: 0 0 auto 0;
    height: 800px;
    background:
      radial-gradient(ellipse 70% 55% at 50% 25%, var(--code-teal) 0%, transparent 75%),
      linear-gradient(180deg, var(--code-navy) 0%, #0a1620 45%, var(--ink-deep) 100%);
  }
  .door-room {
    position: absolute;
    left: 0;
    right: 0;
    bottom: 0;
    height: 430px;
    background:
      radial-gradient(ellipse 48% 22% at 50% 52%, rgba(201, 220, 230, 0.55) 0%, rgba(201, 220, 230, 0.15) 55%, transparent 80%),
      linear-gradient(180deg, var(--ink-deep) 0%, var(--room-dark) 40%, #10262f 72%, var(--floor-teal) 100%);
  }
  .author {
    position: absolute;
    top: 228px;
    left: 0;
    width: 662px;
    margin: 0;
    text-align: right;
    font-family: "Ubuntu", sans-serif;
    font-weight: 400;
    font-size: 60px;
    letter-spacing: 0.5px;
    color: var(--author-blue);
  }
  .title {
    position: absolute;
    top: 400px;
    left: 0;
    width: 750px;
    height: 300px;
    margin: 0;
    overflow: visible;
  }
  .title text {
    font-family: "Doto", monospace;
    font-weight: 900;
    fill: var(--title-white);
  }
  .genre {
    position: absolute;
    top: 704px;
    left: 450px;
    margin: 0;
    font-family: "Tinos", serif;
    font-size: 32px;
    letter-spacing: 1px;
    color: var(--roman-blue);
  }
</style>
</head>
<body>
  <main class="cover">
    <div class="code-field" role="img" aria-label="Dunkler Hintergrund aus herabfallenden Binärcode-Zeilen in Blautönen"></div>
    <div class="door-room" role="img" aria-label="Vier weiße, nebeneinanderliegende Bürotüren in einem kühlen, dunklen Raum mit blaugrünem Boden"></div>

    <p class="author">K.J. Brandau</p>

    <svg class="title" viewBox="0 400 750 300" width="750" height="300" role="heading" aria-level="1" aria-label="Die Schwelle">
      <defs>
        <filter id="screen-glow" x="-10%" y="-30%" width="120%" height="160%">
          <feGaussianBlur in="SourceGraphic" stdDeviation="3" result="blur"/>
          <feFlood flood-color="#bee1f5" flood-opacity="0.55"/>
          <feComposite in2="blur" operator="in" result="glow"/>
          <feMerge>
            <feMergeNode in="glow"/>
            <feMergeNode in="SourceGraphic"/>
          </feMerge>
        </filter>
      </defs>
      <g filter="url(#screen-glow)">
        <text x="132" y="494" font-size="100" textLength="140" lengthAdjust="spacingAndGlyphs">Die</text>
        <text x="96" y="670" font-size="180" textLength="566" lengthAdjust="spacingAndGlyphs">Schwelle</text>
      </g>
    </svg>

    <p class="genre">ROMAN</p>
  </main>
</body>
</html>
```